Velvet Glow Co. Derma Roller packaging design

I need a box designed for a skin care brand called Velvet Glow Co. The box will be for our Derma Roller- a skin rejuvenation device. It will be sold online with lots of competition. I would like a modern, high end design, something that stands out and looks amazing. My logo is blush pink and black, for packaging i need no more than 3 colours, maybe gold if any other colour is used. A photo of a sample derma roller is attached below for an idea of what the product looks like, however my roller with have a clear handle with a black roller. The roller comes in a clear case, the box dimensions will need to be 16 cm long, 4 cm high, 4.5 cm wide.
ATTACHED ARE 2 SAMPLE BOXES AS AN EXAMPLE OF THE SIZE OF BOX REQUIRED!

Target Market(s)

25-50 year old women in the US

Colors
e667a6
000000
efefef

Requirements
Must have
• LOGO
• NAME OF PRODUCT- Cosmetic Derma Roller
• NEEDLE DEPTH- 0.25mm
• CAUTION- For personal use only, Do not use if allergic to metal, Do not use on open skin, wounds or active acne, sterilise roller before and after use.
Nice to have
• BENEFITS- Skin Rejuvenation, Collagen Induction Therapy, Increase product absorption, reduce acne scars and pigmentation
• FEATURES- 540 high quality titanium needles, ultra sharp needle tips, cross-line needle arrangement, ergonomic handle, anti slip grip,

```html
<!DOCTYPE html>
<html lang="en">
<head>
<meta charset="utf-8">
<title>Velvet Glow Co. – Cosmetic Derma Roller Box</title>
<link href="https://fonts.googleapis.com/css2?family=Oswald:wght@400;500&display=swap" rel="stylesheet">
<style>
  :root {
    --bg: #f8f2f0;
    --blush: #eed0cd;
    --cream: #fcf4ee;
    --ink: #1c1717;
    --gold-dark: #c48a76;
    --gold-mid: #e4b3a0;
    --gold-light: #fbe3d6;
  }
  * { margin: 0; padding: 0; box-sizing: border-box; }
  html, body { width: 1200px; height: 1200px; overflow: hidden; }
  body {
    background: radial-gradient(ellipse at center, #ffffff 0%, var(--bg) 75%);
    font-family: "Oswald", sans-serif;
    position: relative;
  }
  .box-face {
    position: absolute;
    left: 50px;
    width: 1104px;
    height: 356px;
    display: flex;
    box-shadow: 0 6px 14px rgba(80, 60, 60, 0.35);
  }
  .box-face--front { top: 180px; }
  .box-face--back { top: 662px; }
  .end-panel { width: 210px; background: var(--blush); }
  .foil-strip {
    width: 17px;
    background: linear-gradient(180deg, var(--gold-dark) 0%, var(--gold-mid) 35%, var(--gold-light) 60%, var(--gold-dark) 100%);
  }
  .main-panel {
    flex: 1;
    background: var(--cream);
    position: relative;
  }
  .brand {
    position: absolute;
    top: 118px;
    left: 0; right: 0;
    display: flex;
    align-items: center;
    justify-content: center;
    gap: 12px;
    font-size: 30px;
    font-weight: 400;
    letter-spacing: 3px;
    color: var(--ink);
  }
  .brand-square {
    width: 14px; height: 14px;
    background: var(--blush);
  }
  .product-title {
    position: absolute;
    left: 0; right: 0;
    text-align: center;
    font-size: 30px;
    font-weight: 500;
    letter-spacing: 0.5px;
    line-height: 1;
    background: linear-gradient(90deg, var(--gold-light) 0%, var(--gold-mid) 40%, var(--gold-dark) 75%, var(--gold-mid) 100%);
    -webkit-background-clip: text;
    background-clip: text;
    color: transparent;
    transform: scaleX(0.82);
  }
  .box-face--front .product-title { top: 264px; }
  .box-face--back .product-title { top: 54px; }
  .product-info {
    position: absolute;
    left: 56px;
    top: 118px;
    width: 570px;
    font-size: 15.5px;
    font-weight: 400;
    line-height: 23px;
    color: var(--ink);
    text-transform: uppercase;
    transform: scaleX(0.86);
    transform-origin: left top;
    width: 660px;
  }
  .product-info p + p { margin-top: 23px; }
</style>
</head>
<body>
  <section class="box-face box-face--front">
    <div class="end-panel"></div>
    <div class="foil-strip"></div>
    <div class="main-panel">
      <div class="brand"><span class="brand-square"></span>Velvet Glow Co.</div>
      <h1 class="product-title">Cosmetic Derma Roller</h1>
    </div>
    <div class="foil-strip"></div>
    <div class="end-panel"></div>
  </section>

  <section class="box-face box-face--back">
    <div class="end-panel"></div>
    <div class="foil-strip"></div>
    <div class="main-panel">
      <h2 class="product-title">Cosmetic Derma Roller</h2>
      <div class="product-info">
        <p>Benefits: skin rejuvenation, collagen induction therapy, increase product absorption, reduce acne scars and pigmentation</p>
        <p>Features: 540 high quality 0.25 mm titanium needles, ultra sharp needle tips, cross-line needle arrangement, ergonomic handle, anti slip grip</p>
        <p>Caution: for personal use only, do not use if allergic to metal, do not use on open skin, wounds or active acne, sterilise roller before and after use.</p>
      </div>
    </div>
    <div class="foil-strip"></div>
    <div class="end-panel"></div>
  </section>
</body>
</html>
```